Business Card Design using new attached logo

We are a family run Plumbing and Heating firm looking to improve our company image with an improved business card and new logo.We are looking to keep the company colour (Blue) involved in our design

Reason: New logo added which needs to be incorporated on designs

Industry/Entity Type

Business

Contact Information for Business Card

See attachment of all info required.

Requirements
Must have
• We have just picked a new company logo which is attached.
• Could you please provide your business card designs using this logo.
• We are looking for the logo on the back as well as the front with all the info required

```html
<!DOCTYPE html>
<html lang="en">
<head>
<meta charset="utf-8">
<title>KDL Heating Ltd. – Business Card</title>
<link href="https://fonts.googleapis.com/css2?family=Poppins:wght@400;600;700&display=swap" rel="stylesheet">
<style>
  :root {
    --page-bg: #e9e9e7;
    --card-black: #050505;
    --brand-blue: #22aee8;
    --back-blue-light: #38c4f6;
    --back-blue-dark: #19a3e3;
    --ink-navy: #0c1a2c;
    --white: #ffffff;
    --art-fill: #1d2638;
  }
  * { box-sizing: border-box; margin: 0; padding: 0; }
  html, body {
    width: 1200px; height: 856px; overflow: hidden;
    background: var(--page-bg);
    font-family: "Poppins", Arial, sans-serif;
  }
  .sheet {
    width: 1200px; height: 856px;
    display: flex; align-items: center; justify-content: center; gap: 40px;
  }
  .card {
    position: relative;
    width: 520px; height: 316px;
    border-radius: 30px;
    overflow: hidden;
    box-shadow: 0 6px 18px rgba(0,0,0,0.18);
  }
  /* Front */
  .card-front { background: var(--card-black); }
  .hero-art {
    position: absolute; left: 34px; top: 50px;
    width: 240px; height: 216px;
    border-radius: 12px;
    background: var(--art-fill);
  }
  .brand-name {
    position: absolute; left: 298px; top: 66px;
    color: var(--brand-blue);
    font-weight: 700; font-size: 38px; line-height: 38px;
    text-transform: uppercase; letter-spacing: 1px;
  }
  .person {
    position: absolute; left: 316px; top: 196px;
    color: var(--white);
  }
  .person-name { font-weight: 600; font-size: 15px; letter-spacing: 0.5px; }
  .person-role { font-weight: 400; font-size: 13px; margin-top: -2px; }
  /* Back */
  .card-back {
    background: linear-gradient(180deg, var(--back-blue-light), var(--back-blue-dark));
    color: var(--ink-navy);
    display: flex; flex-direction: column; align-items: center; justify-content: center;
    font-size: 13.5px; font-weight: 600; text-align: center;
  }
  .contact-line { display: flex; align-items: center; gap: 6px; }
  .contact-line + .contact-line { margin-top: 4px; }
  .contact-line.primary { margin-bottom: 44px; }
  .contact-gap { width: 14px; }
  .icon { width: 12px; height: 12px; flex: none; }
</style>
</head>
<body>
<main class="sheet">
  <section class="card card-front" aria-label="Card front">
    <div class="hero-art" role="img" aria-label="Illustration of water and fire"></div>
    <div class="brand-name">KDL<br>Heating<br>Ltd.</div>
    <div class="person">
      <p class="person-name">OWEN HARPER</p>
      <p class="person-role">Director</p>
    </div>
  </section>

  <section class="card card-back" aria-label="Card back">
    <p class="contact-line primary">
      <svg class="icon" viewBox="0 0 12 12" aria-hidden="true"><circle cx="6" cy="6" r="6" fill="#0c1a2c"/><path d="M4 3.2l1 1.4-.6.7c.4.9 1.1 1.6 2 2l.7-.6 1.4 1-.5.9c-2.3-.3-4.1-2.1-4.4-4.4z" fill="#fff"/></svg>
      <span>07700 900123</span>
      <span class="contact-gap"></span>
      <svg class="icon" viewBox="0 0 12 12" aria-hidden="true"><circle cx="6" cy="6" r="6" fill="#0c1a2c"/><rect x="3" y="4" width="6" height="4.2" fill="#fff"/><path d="M3 4l3 2.3L9 4" stroke="#0c1a2c" stroke-width="0.7" fill="none"/></svg>
      <span>owen@kdlheating.co.uk</span>
    </p>
    <p class="contact-line">12 Mill Parade, Elm Road, Redford, Surrey RD0 4XY</p>
    <p class="contact-line">
      <svg class="icon" viewBox="0 0 12 12" aria-hidden="true"><circle cx="6" cy="6" r="6" fill="#0c1a2c"/><path d="M4 3.2l1 1.4-.6.7c.4.9 1.1 1.6 2 2l.7-.6 1.4 1-.5.9c-2.3-.3-4.1-2.1-4.4-4.4z" fill="#fff"/></svg>
      <span>020 7946 0321</span>
      <svg class="icon" viewBox="0 0 12 12" aria-hidden="true"><circle cx="6" cy="6" r="6" fill="#0c1a2c"/><rect x="3.2" y="5" width="5.6" height="3.4" fill="#fff"/><rect x="4.2" y="3.2" width="3.6" height="1.6" fill="#fff"/></svg>
      <span>020 7946 0322</span>
    </p>
  </section>
</main>
</body>
</html>
```